Rollers & Glides.com

Vertical Business Card with focus on branding with our icon. Information on card will be logo, persons name, position, phone number, email address and website. Use the the name Marcus Pellow, position President, phone number 480.915.2267, email Marcus@rollersandglides-demo.com, website www.rollersandglides-demo.com.

```html
<!DOCTYPE html>
<html lang="en">
<head>
<meta charset="utf-8">
<title>Rollers &amp; Glides.com — Business Card</title>
<link rel="stylesheet" href="https://fonts.googleapis.com/css2?family=Arimo:wght@400;700&display=swap">
<style>
  :root {
    --backdrop: #2b2726;
    --card: #1b1b1b;
    --brand-blue: #3461b3;
    --name-blue: #1f74c4;
    --ink-light: #f2f2f2;
    --rule: #8a8a8a;
  }
  * { margin: 0; padding: 0; box-sizing: border-box; }
  html, body {
    width: 1200px; height: 842px; overflow: hidden;
    background: var(--backdrop);
    font-family: "Arimo", Arial, sans-serif;
  }
  .canvas {
    position: relative; width: 1200px; height: 842px;
    display: flex; align-items: center; justify-content: center; gap: 50px;
  }
  .card {
    position: relative; width: 525px; height: 300px;
    background: var(--card); overflow: hidden;
    box-shadow: 0 14px 30px rgba(0,0,0,0.55);
  }
  /* Contact side */
  .band { position: absolute; left: 0; right: 0; height: 14px; background: var(--brand-blue); }
  .band--top { top: 0; }
  .band--bottom { bottom: 0; }
  .contact {
    position: absolute; inset: 0;
    display: flex; flex-direction: column; align-items: center; justify-content: center;
    text-align: center; color: var(--ink-light);
  }
  .contact__name {
    font-weight: 700; font-size: 26px; letter-spacing: 0.5px;
    text-transform: uppercase; color: var(--name-blue); line-height: 1;
  }
  .contact__role { font-size: 19px; margin-top: 2px; }
  .contact__rule { width: 170px; height: 1px; background: var(--rule); margin: 14px 0 12px; }
  .contact__line { font-size: 18px; line-height: 1.22; }
  .contact__line .accent { color: var(--brand-blue); }
  /* Brand side */
  .tab { position: absolute; width: 40px; height: 40px; background: var(--brand-blue); }
  .tab--left { left: 0; top: 182px; }
  .tab--right { right: 0; top: 46px; }
  .brand {
    position: absolute; inset: 0;
    display: flex; align-items: center; justify-content: center;
  }
  .brand__name {
    font-size: 32px; font-weight: 400; letter-spacing: 1px;
    color: var(--brand-blue);
  }
</style>
</head>
<body>
<main class="canvas">
  <section class="card card--contact">
    <div class="band band--top"></div>
    <div class="contact">
      <h1 class="contact__name">Marcus Pellow</h1>
      <p class="contact__role">President</p>
      <div class="contact__rule"></div>
      <p class="contact__line">480.915.2267</p>
      <p class="contact__line">Marcus@rollersandglides-demo.com</p>
      <p class="contact__line">www.<span class="accent">rollersandglides-demo</span>.com</p>
    </div>
    <div class="band band--bottom"></div>
  </section>

  <section class="card card--brand">
    <div class="tab tab--right"></div>
    <div class="tab tab--left"></div>
    <div class="brand">
      <p class="brand__name">Rollers &amp; Glides.com</p>
    </div>
  </section>
</main>
</body>
</html>
```